Business Card Design

We are a commercial real estate brokerage in San Francisco, leasing office buildings downtown.
I would like a clean, elegant look. Simple but powerful .

Industry/Entity Type

Business

Contact Information for Business Card

Derek Holloway
lic# 07258143
415.555.0172
derek@velt-commercial.example
velt-commercial.example

```html
<!DOCTYPE html>
<html lang="en">
<head>
<meta charset="utf-8">
<title>Velt Commercial — Business Card</title>
<link href="https://fonts.googleapis.com/css2?family=Source+Sans+3:wght@400;600&display=swap" rel="stylesheet">
<style>
  :root {
    --backdrop-top: #1e1e1e;
    --backdrop-bottom: #050505;
    --card-front: #ffffff;
    --card-back: #f3f3f3;
    --brand-blue: #6a7c9a;
    --ink: #4a4a4a;
    --icon: #6f7a8c;
    --back-mark: #dcdcdc;
  }
  * { margin: 0; padding: 0; box-sizing: border-box; }
  html, body { width: 1200px; height: 900px; overflow: hidden; }
  body {
    background: linear-gradient(180deg, var(--backdrop-top) 0%, var(--backdrop-bottom) 100%);
    font-family: "Source Sans 3", "Myriad Pro", Arial, sans-serif;
    position: relative;
  }
  .card {
    position: absolute;
    top: 306px;
    width: 440px;
    height: 271px;
    border-radius: 12px;
  }
  .card--front { left: 149px; background: var(--card-front); }
  .card--back { left: 608px; width: 441px; background: var(--card-back); }

  .brand {
    position: absolute;
    display: flex;
    flex-direction: column;
    color: var(--brand-blue);
    font-weight: 600;
    line-height: 1;
  }
  .card--front .brand { left: 22px; top: 112px; }
  .brand__name { font-size: 36px; letter-spacing: 1px; }
  .brand__sub { font-size: 16px; letter-spacing: 1.2px; margin-top: 2px; }

  .card--back .brand {
    left: 0; right: 0; top: 96px;
    align-items: center;
    color: var(--back-mark);
  }
  .card--back .brand__name { font-size: 56px; letter-spacing: 2px; }
  .card--back .brand__sub { font-size: 24px; letter-spacing: 2px; margin-top: 4px; }

  .contact {
    position: absolute;
    left: 218px;
    top: 80px;
    color: var(--ink);
    font-size: 13px;
  }
  .contact__name {
    color: var(--brand-blue);
    font-weight: 600;
    font-size: 16px;
    margin-bottom: 12px;
  }
  .contact__licence { margin-bottom: 16px; }
  .contact__list { list-style: none; }
  .contact__item {
    display: flex;
    align-items: center;
    gap: 9px;
    line-height: 16px;
  }
  .contact__item svg { width: 9px; height: 9px; fill: var(--icon); flex: none; }
</style>
</head>
<body>
  <section class="card card--front" aria-label="Card front">
    <div class="brand">
      <span class="brand__name">VELT</span>
      <span class="brand__sub">COMMERCIAL</span>
    </div>
    <div class="contact">
      <p class="contact__name">Derek Holloway</p>
      <p class="contact__licence">Lic# 07258143</p>
      <ul class="contact__list">
        <li class="contact__item">
          <svg viewBox="0 0 10 10" aria-hidden="true"><path d="M2 0.5l2 2-1 1.2a6 6 0 0 0 3.3 3.3l1.2-1 2 2-1.3 1.5C4.5 9.5 0.5 5.5 0.5 1.8z"/></svg>
          <span>415.555.0172</span>
        </li>
        <li class="contact__item">
          <svg viewBox="0 0 10 10" aria-hidden="true"><path d="M0.5 2h9v6h-9z M0.5 2l4.5 3.5L9.5 2" fill="none" stroke="#6f7a8c" stroke-width="1.2"/></svg>
          <span>derek@velt-commercial.example</span>
        </li>
        <li class="contact__item">
          <svg viewBox="0 0 10 10" aria-hidden="true"><circle cx="5" cy="5" r="4.2" fill="none" stroke="#6f7a8c" stroke-width="1"/><path d="M0.8 5h8.4M5 0.8v8.4" stroke="#6f7a8c" stroke-width="0.8"/></svg>
          <span>velt-commercial.example</span>
        </li>
      </ul>
    </div>
  </section>

  <section class="card card--back" aria-label="Card back">
    <div class="brand">
      <span class="brand__name">VELT</span>
      <span class="brand__sub">COMMERCIAL</span>
    </div>
  </section>
</body>
</html>
```